Heritage Hollow Business Cards

Require a business card design. <br/><br/>Needs to include logo (either round or long version) plus these details:<br/>Maya Torvell<br/>Heritage Hollow<br/>maya@kelvadtrading.com.au<br/>02 6481 7395<br/>PO Box Glenwarra NSW 2791<br/>www.heritagehollow.com.au<br/><br/>I need in an editable format so that I can create for multiple staff members. <br/><br/>

Target Market(s)

We are an online store selling renovation products to home owners are builders. Looking for a classic classy design.

Industry/Entity Type

Home And Garden

Contact Information for Business Card

Maya Torvell
Heritage Hollow
maya@kelvadtrading.com.au
02 6481 7395
PO Box Glenwarra NSW 2791
www.heritagehollow.com.au

Colors

Designer to choose colors to be used in the design.

Requirements
Must have
• Must include Logo.

```html
<!DOCTYPE html>
<html lang="en">
<head>
<meta charset="utf-8">
<title>Heritage Hollow Business Cards</title>
<link rel="stylesheet" href="https://fonts.googleapis.com/css2?family=Merriweather:wght@700;900&family=Open+Sans:wght@400&display=swap">
<style>
  :root {
    --backdrop: #1c1c1d;
    --card: #ffffff;
    --ink: #2b2b2b;
    --charcoal: #231f20;
    --green: #12876a;
    --name-green: #3f6b57;
    --rule: #bdbdbd;
    --muted: #3a3a3a;
  }
  * { margin: 0; padding: 0; box-sizing: border-box; }
  html, body { width: 1200px; height: 960px; overflow: hidden; }
  body {
    background: var(--backdrop);
    font-family: "Open Sans", Arial, sans-serif;
    position: relative;
  }
  .card {
    position: absolute;
    left: 280px;
    width: 640px;
    height: 366px;
    background: var(--card);
    overflow: hidden;
    box-shadow: 0 12px 30px rgba(0,0,0,.45);
  }
  .card--front { top: 90px; }
  .card--back { top: 504px; }

  .front-brand {
    position: absolute;
    left: 0; right: 0; top: 150px;
    text-align: center;
    font-family: "Merriweather", Georgia, serif;
    font-weight: 900;
    font-size: 44px;
    color: var(--ink);
    letter-spacing: .5px;
  }

  .swoosh { position: absolute; left: 0; top: 0; width: 640px; height: 366px; }

  .back-brand {
    position: absolute;
    left: 44px; top: 70px;
    display: flex; align-items: center; gap: 14px;
  }
  .back-brand__mark {
    width: 34px; height: 34px;
    border: 2px solid var(--ink);
    border-radius: 50%;
    flex: none;
  }
  .back-brand__name {
    font-family: "Merriweather", Georgia, serif;
    font-weight: 900;
    font-size: 30px;
    line-height: 1.05;
    color: var(--ink);
  }

  .divider {
    position: absolute;
    left: 316px; top: 118px;
    width: 1px; height: 122px;
    background: var(--rule);
  }

  .details {
    position: absolute;
    left: 334px; top: 112px;
    color: var(--muted);
  }
  .details__name {
    font-family: "Merriweather", Georgia, serif;
    font-weight: 700;
    font-size: 21px;
    color: var(--name-green);
    line-height: 1.1;
  }
  .details__role {
    font-family: "Merriweather", Georgia, serif;
    font-weight: 700;
    font-size: 12px;
    color: var(--ink);
    margin-bottom: 8px;
  }
  .details__address { font-size: 14px; line-height: 1.3; margin-bottom: 4px; }
  .contact-list { list-style: none; }
  .contact-list li {
    display: flex; align-items: center; gap: 8px;
    font-size: 14px; line-height: 1.45;
  }
  .contact-list svg { width: 12px; height: 12px; flex: none; }
</style>
</head>
<body>

  <section class="card card--front" aria-label="Card front">
    <div class="front-brand">Heritage Hollow</div>
  </section>

  <section class="card card--back" aria-label="Card back">
    <svg class="swoosh" viewBox="0 0 640 366" aria-hidden="true">
      <path d="M0 188 C 70 215, 120 300, 300 312 C 450 322, 560 330, 640 366 L 0 366 Z" fill="var(--green)"/>
      <path d="M0 208 C 60 240, 110 312, 300 322 C 450 330, 560 340, 640 366 L 0 366 Z" fill="#ffffff"/>
      <path d="M0 212 C 60 246, 110 318, 300 328 C 450 336, 560 346, 640 366 L 0 366 Z" fill="var(--charcoal)"/>
    </svg>

    <div class="back-brand">
      <span class="back-brand__mark"></span>
      <span class="back-brand__name">Heritage<br>Hollow</span>
    </div>

    <div class="divider"></div>

    <div class="details">
      <div class="details__name">Maya Torvell</div>
      <div class="details__role">Director</div>
      <div class="details__address">PO Box Glenwarra<br>NSW 2791</div>
      <ul class="contact-list">
        <li>
          <svg viewBox="0 0 24 24" aria-hidden="true"><path fill="var(--green)" d="M6.6 10.8c1.4 2.8 3.8 5.1 6.6 6.6l2.2-2.2c.3-.3.7-.4 1-.2 1.1.4 2.3.6 3.6.6.6 0 1 .4 1 1V20c0 .6-.4 1-1 1C10.6 21 3 13.4 3 4c0-.6.4-1 1-1h3.5c.6 0 1 .4 1 1 0 1.3.2 2.5.6 3.6.1.3 0 .7-.2 1l-2.3 2.2z"/></svg>
          02 6481 7395
        </li>
        <li>
          <svg viewBox="0 0 24 24" aria-hidden="true"><path fill="var(--green)" d="M2 5h20v14H2z"/><path fill="none" stroke="#fff" stroke-width="1.6" d="M2 5l10 8 10-8"/></svg>
          maya@kelvadtrading.com.au
        </li>
        <li>
          <svg viewBox="0 0 24 24" aria-hidden="true"><circle cx="12" cy="12" r="10" fill="var(--green)"/><path fill="none" stroke="#fff" stroke-width="1.4" d="M2 12h20M12 2c3 3 3 17 0 20M12 2c-3 3-3 17 0 20"/></svg>
          www.heritagehollow.com.au
        </li>
      </ul>
    </div>
  </section>

</body>
</html>
```